Dynamic Business Card for Sports Supplements Company

Hi! I'm looking for an awesome business card to match my existing sports supplement company. I have uploaded my current company logo and screenshot of the front page of my website.

I would like to have something dynamic and interesting and utilize the colors in the website - the reds and purples

The business card should be double sided and focus on a unique eye-catching design on the back and include all the relevant company info.

Most importantly, it should say somewhere: "Sign up on our website for a coupon code."

Target Market(s)

Mostly for women gym goers but it shouldn't be too feminine. It should be in keeping with the website design. It should flow and clearly be connected to it

Industry/Entity Type

Business

Contact Information for Business Card

Lorraine K. Vestal
CEO
LVestal@Quorvanexco.com
www.quorvanexco.com
555.417.3820
P.O. Box 47315
Harlow Vale, Easton 00000

Sign up on our website for a coupon code

Font styles to use
Serif
Sans Serif
Other font styles liked:
• Novecento font family and "Quorvanex" is in AR Destine font

Requirements
Must have
• One side should be a bold Quorvanex logo design. Even just the symbol itself may be o.k. (see attached file)

```html
<!DOCTYPE html>
<html lang="en">
<head>
<meta charset="utf-8">
<title>Quorvanex Business Card</title>
<link rel="stylesheet" href="https://fonts.googleapis.com/css2?family=Montserrat:wght@400;500;600;800&display=swap">
<style>
  :root {
    --stage: #2e2e2e;
    --card-black: #050505;
    --card-white: #ffffff;
    --brand-red: #e0262b;
    --ink: #111111;
    --ink-soft: #7a7a7a;
    --on-dark: #ffffff;
  }
  * { margin: 0; padding: 0; box-sizing: border-box; }
  html, body { width: 1200px; height: 855px; overflow: hidden; }
  body {
    background: var(--stage);
    font-family: "Montserrat", sans-serif;
    position: relative;
  }
  .card {
    position: absolute;
    width: 560px;
    height: 320px;
    box-shadow: 0 14px 30px rgba(0,0,0,0.45);
  }
  .card-back {
    left: 70px; top: 90px;
    background: var(--card-black);
    display: flex; align-items: center; justify-content: center; gap: 26px;
  }
  .brand-mark {
    display: flex; align-items: center; gap: 10px;
  }
  .brand-mark .square {
    width: 22px; height: 22px; background: var(--brand-red);
  }
  .card-back .brand-name {
    color: var(--on-dark); font-weight: 800; font-size: 22px; letter-spacing: 1px;
  }
  .coupon-note {
    color: var(--on-dark); font-size: 16px; line-height: 1.35; letter-spacing: 0.5px;
  }
  .card-front {
    left: 570px; top: 445px;
    background: var(--card-white);
    color: var(--ink);
  }
  .card-front .brand-mark {
    position: absolute; right: 36px; top: 48px;
  }
  .card-front .brand-name {
    color: var(--ink); font-weight: 800; font-size: 28px; letter-spacing: 1px;
  }
  .contact {
    position: absolute; left: 40px; top: 138px;
  }
  .person-name { font-size: 20px; font-weight: 600; }
  .person-title { font-size: 14px; color: var(--ink-soft); margin-top: 2px; }
  .address { font-size: 14px; color: var(--ink-soft); margin-top: 14px; line-height: 1.35; }
  .links { list-style: none; margin-top: 12px; font-size: 14px; color: var(--ink-soft); line-height: 1.45; }
  .links li { display: flex; align-items: center; gap: 8px; }
  .links svg { width: 12px; height: 12px; flex: none; }
</style>
</head>
<body>
  <section class="card card-back">
    <div class="brand-mark">
      <span class="square"></span>
      <span class="brand-name">Quorvanex</span>
    </div>
    <p class="coupon-note">Sign up on our website<br>for a coupon code</p>
  </section>

  <section class="card card-front">
    <div class="brand-mark">
      <span class="square"></span>
      <span class="brand-name">QUORVANEX</span>
    </div>
    <div class="contact">
      <p class="person-name">Lorraine K. Vestal</p>
      <p class="person-title">CEO</p>
      <p class="address">P.O. Box 47315<br>Harlow Vale, Easton 00000</p>
      <ul class="links">
        <li>
          <svg viewBox="0 0 12 12" aria-hidden="true"><path d="M2 1 L4.5 1 L5 3.5 L3.8 4.5 Q5 7 7.5 8.2 L8.5 7 L11 7.5 L11 10 Q6 11 2.5 7.5 Q0.5 5 2 1Z" fill="var(--brand-red)"/></svg>
          555.417.3820
        </li>
        <li>
          <svg viewBox="0 0 12 12" aria-hidden="true"><rect x="0.5" y="2" width="11" height="8" fill="var(--brand-red)"/><path d="M0.5 2 L6 6.5 L11.5 2" fill="none" stroke="#fff" stroke-width="1"/></svg>
          LVestal@Quorvanexco.com
        </li>
        <li>
          <svg viewBox="0 0 12 12" aria-hidden="true"><g fill="none" stroke="var(--brand-red)" stroke-width="1.1"><circle cx="6" cy="6" r="5"/><ellipse cx="6" cy="6" rx="2.2" ry="5"/><path d="M1 6 H11 M2 3.3 H10 M2 8.7 H10"/></g></svg>
          www.quorvanexco.com
        </li>
      </ul>
    </div>
  </section>
</body>
</html>
```